Help me make landing pages for my web application that are mobile friendly

I need to make 2 mobile friendly landing pages for an application. The 2 pages will be related. First I need a home page and then I need a working page. I do not want to change the color scheme or logos. Just layout and design.

```html
<!DOCTYPE html>
<html lang="en">
<head>
<meta charset="utf-8">
<title>My Assignments</title>
<link href="https://fonts.googleapis.com/css2?family=Poppins:wght@400;500;600;700&display=swap" rel="stylesheet">
<style>
:root{
  --ink:#2b2b2b;
  --muted:#5d5d5d;
  --brand:#26aed0;
  --name:#2ba9cb;
  --tab-off:#d8e0e3;
  --card:#ffffff;
  --line:#d6d6d6;
  --active:#7ec87a;
  --canceled:#c8141e;
  --complete:#f5a84a;
  --nav-on:#7b5cc4;
  --nav-off:#8a8a8a;
  --check:#5fa83a;
}
*{margin:0;padding:0;box-sizing:border-box}
html,body{width:1200px;height:2802px;overflow:hidden}
body{font-family:"Poppins",sans-serif;color:var(--ink);background:#fff}
.screen{position:relative;width:1200px;height:2802px;overflow:hidden;
  background:
   radial-gradient(ellipse 700px 900px at 1200px 0,#d3eef6 0%,rgba(211,238,246,0) 75%),
   radial-gradient(ellipse 700px 900px at 0 2700px,#e7e4f8 0%,rgba(231,228,248,0) 75%),
   #fbfcfd}
.notch{position:absolute;left:0;top:0;width:892px;height:96px;background:#fff;border-bottom-right-radius:46px}
.time{position:absolute;left:143px;top:38px;font-size:40px;font-weight:600}
.status-icons{position:absolute;left:918px;top:46px}
.topbar{position:absolute;left:62px;top:160px;display:flex;align-items:center;gap:18px;font-size:31px;font-weight:700}
.bell{position:absolute;left:1088px;top:152px}
.tabs{position:absolute;left:64px;top:262px;width:1072px;display:flex;gap:18px}
.tab{height:95px;border-radius:48px;display:flex;align-items:center;justify-content:center;font-size:29px;font-weight:600}
.tab-on{width:518px;background:var(--brand);color:#fff}
.tab-off{width:536px;background:var(--tab-off);color:#333}
.section-title{position:absolute;left:64px;top:426px;font-size:40px;font-weight:700}
.card{position:absolute;left:66px;width:1068px;height:428px;background:var(--card);border:2px solid #e2e2e2;border-radius:51px;box-shadow:0 6px 20px rgba(0,0,0,.03)}
.card>*{position:absolute}
.subbing{left:71px;top:44px;font-size:27px;font-weight:600}
.edit{left:950px;top:33px;width:66px;height:66px;border-radius:50%;background:#eeeeee;display:flex;align-items:center;justify-content:center}
.photo{left:73px;top:115px;width:234px;height:234px;border-radius:40px}
.check{left:282px;top:119px}
.name{left:349px;top:118px;font-size:37px;font-weight:700;color:var(--name)}
.role{left:349px;top:173px;font-size:26px;color:var(--muted)}
.divider{left:355px;top:236px;width:655px;height:2px;background:var(--line)}
.label{top:257px;font-size:27px;font-weight:600}
.l-loc{left:348px}.l-stat{left:534px}.l-time{left:748px}
.loc{left:350px;top:307px;font-size:21px}
.slot{left:748px;top:303px;font-size:23px}
.badge{left:536px;top:309px;width:119px;height:48px;border-radius:24px;color:#fff;font-size:22px;font-weight:700;display:flex;align-items:center;justify-content:center}
.b-active{background:var(--active)}
.b-canceled{background:var(--canceled)}
.b-complete{background:var(--complete)}
.scrollbar{position:absolute;left:1159px;top:1359px;width:7px;height:150px;border-radius:4px;background:#2a2a2a}
.nav{position:absolute;left:0;top:2617px;width:1200px;height:185px;background:#fff;border-top:2px solid #e4e4e4}
.nav-item{position:absolute;top:50px;transform:translateX(-50%);display:flex;flex-direction:column;align-items:center;gap:14px;font-size:26px;font-weight:600;color:var(--nav-off)}
.nav-item.on{color:var(--nav-on)}
</style>
</head>
<body>
<div class="screen">
  <div class="notch"></div>
  <div class="time">9:41</div>
  <svg class="status-icons" width="190" height="34" viewBox="0 0 190 34">
    <rect x="0" y="22" width="7" height="10" rx="2" fill="#111"/>
    <rect x="11" y="16" width="7" height="16" rx="2" fill="#111"/>
    <rect x="22" y="9" width="7" height="23" rx="2" fill="#111"/>
    <rect x="33" y="2" width="7" height="30" rx="2" fill="#111"/>
    <path d="M58 12a26 26 0 0 1 38 0l-4 4a20 20 0 0 0-30 0z M65 19a16 16 0 0 1 24 0l-4 4a10 10 0 0 0-16 0z M72 26a6 6 0 0 1 10 0l-5 6z" fill="#111"/>
    <rect x="118" y="4" width="58" height="26" rx="7" fill="none" stroke="#888" stroke-width="2.5"/>
    <rect x="122" y="8" width="50" height="18" rx="4" fill="#111"/>
    <rect x="179" y="12" width="4" height="10" rx="2" fill="#888"/>
  </svg>

  <div class="topbar">
    <svg width="20" height="28" viewBox="0 0 20 28"><path d="M15 4L5 14l10 10" fill="none" stroke="#2b2b2b" stroke-width="4" stroke-linecap="round" stroke-linejoin="round"/></svg>
    <span>MESSAGE</span>
  </div>
  <svg class="bell" width="50" height="60" viewBox="0 0 50 60">
    <path d="M25 8c-10 0-15 8-15 17v10l-5 7h40l-5-7V25c0-9-5-17-15-17z" fill="#111"/>
    <path d="M19 46a6 6 0 0 0 12 0z" fill="#111"/>
    <circle cx="25" cy="7" r="7" fill="#e0303a"/>
  </svg>

  <div class="tabs">
    <div class="tab tab-on">My Assignments</div>
    <div class="tab tab-off">Available Openings</div>
  </div>

  <h1 class="section-title">My Assignments</h1>

  <article class="card" style="top:512px">
    <div class="subbing">Subbing For:</div>
    <div class="edit"><svg width="28" height="28" viewBox="0 0 28 28"><path d="M5 21l2-7L18 3l6 6-11 11-8 1z M4 25h20" fill="none" stroke="#222" stroke-width="2.2" stroke-linejoin="round"/></svg></div>
    <div class="photo" role="img" aria-label="Portrait photo of the teacher" style="background:linear-gradient(160deg,#8d8d8d,#5a5a5a)"></div>
    <svg class="check" width="33" height="33" viewBox="0 0 33 33"><circle cx="16.5" cy="16.5" r="15" fill="var(--check)" stroke="#fff" stroke-width="3"/><path d="M10 17l4 4 9-9" fill="none" stroke="#fff" stroke-width="3" stroke-linecap="round"/></svg>
    <div class="name">Devon Hale</div>
    <div class="role">Administrator</div>
    <div class="divider"></div>
    <div class="label l-loc">Location:</div><div class="label l-stat">Status:</div><div class="label l-time">Time Slots:</div>
    <div class="loc">NRHS</div>
    <div class="badge b-active">Active</div>
    <div class="slot">07/26 - 08/07 (14h 15m)</div>
  </article>

  <article class="card" style="top:979px">
    <div class="subbing">Subbing For:</div>
    <div class="edit"><svg width="28" height="28" viewBox="0 0 28 28"><path d="M5 21l2-7L18 3l6 6-11 11-8 1z M4 25h20" fill="none" stroke="#222" stroke-width="2.2" stroke-linejoin="round"/></svg></div>
    <div class="photo" role="img" aria-label="Portrait photo of the teacher" style="background:linear-gradient(160deg,#b9b9b9,#5b4a44)"></div>
    <svg class="check" width="33" height="33" viewBox="0 0 33 33"><circle cx="16.5" cy="16.5" r="15" fill="var(--check)" stroke="#fff" stroke-width="3"/><path d="M10 17l4 4 9-9" fill="none" stroke="#fff" stroke-width="3" stroke-linecap="round"/></svg>
    <div class="name">Nadia Corwell</div>
    <div class="role">Teacher</div>
    <div class="divider"></div>
    <div class="label l-loc">Location:</div><div class="label l-stat">Status:</div><div class="label l-time">Time Slots:</div>
    <div class="loc">NRHS</div>
    <div class="badge b-canceled">Canceled</div>
    <div class="slot">07/31 - 07/31 (9h 0m)</div>
  </article>

  <article class="card" style="top:1447px">
    <div class="subbing">Subbing For:</div>
    <div class="edit"><svg width="28" height="28" viewBox="0 0 28 28"><path d="M5 21l2-7L18 3l6 6-11 11-8 1z M4 25h20" fill="none" stroke="#222" stroke-width="2.2" stroke-linejoin="round"/></svg></div>
    <div class="photo" role="img" aria-label="Portrait photo of the teacher" style="background:linear-gradient(160deg,#c9d2d8,#6d5446)"></div>
    <svg class="check" width="33" height="33" viewBox="0 0 33 33"><circle cx="16.5" cy="16.5" r="15" fill="var(--check)" stroke="#fff" stroke-width="3"/><path d="M10 17l4 4 9-9" fill="none" stroke="#fff" stroke-width="3" stroke-linecap="round"/></svg>
    <div class="name">Marcus Ellery</div>
    <div class="role">Teacher</div>
    <div class="divider"></div>
    <div class="label l-loc">Location:</div><div class="label l-stat">Status:</div><div class="label l-time">Time Slots:</div>
    <div class="loc">NRHS</div>
    <div class="badge b-complete">Complete</div>
    <div class="slot">07/31 - 07/31 (9h 0m)</div>
  </article>

  <article class="card" style="top:1916px">
    <div class="subbing">Subbing For:</div>
    <div class="edit"><svg width="28" height="28" viewBox="0 0 28 28"><path d="M5 21l2-7L18 3l6 6-11 11-8 1z M4 25h20" fill="none" stroke="#222" stroke-width="2.2" stroke-linejoin="round"/></svg></div>
    <div class="photo" role="img" aria-label="Portrait photo of the teacher" style="background:linear-gradient(160deg,#d9d6d2,#7c5a44)"></div>
    <svg class="check" width="33" height="33" viewBox="0 0 33 33"><circle cx="16.5" cy="16.5" r="15" fill="var(--check)" stroke="#fff" stroke-width="3"/><path d="M10 17l4 4 9-9" fill="none" stroke="#fff" stroke-width="3" stroke-linecap="round"/></svg>
    <div class="name">Paula Brannon</div>
    <div class="role">Teacher</div>
    <div class="divider"></div>
    <div class="label l-loc">Location:</div><div class="label l-stat">Status:</div><div class="label l-time">Time Slots:</div>
    <div class="loc">NRHS</div>
    <div class="badge b-active">Active</div>
    <div class="slot">07/26 - 08/07 (14h 15m)</div>
  </article>

  <article class="card" style="top:2384px">
    <div class="subbing">Subbing For:</div>
    <div class="edit"><svg width="28" height="28" viewBox="0 0 28 28"><path d="M5 21l2-7L18 3l6 6-11 11-8 1z M4 25h20" fill="none" stroke="#222" stroke-width="2.2" stroke-linejoin="round"/></svg></div>
    <div class="photo" role="img" aria-label="Portrait photo of the teacher" style="background:linear-gradient(160deg,#d4cfcb,#6e4f3e)"></div>
    <svg class="check" width="33" height="33" viewBox="0 0 33 33"><circle cx="16.5" cy="16.5" r="15" fill="var(--check)" stroke="#fff" stroke-width="3"/><path d="M10 17l4 4 9-9" fill="none" stroke="#fff" stroke-width="3" stroke-linecap="round"/></svg>
    <div class="name">Nadia Corwell</div>
    <div class="role">Teacher</div>
  </article>

  <div class="scrollbar"></div>

  <nav class="nav">
    <div class="nav-item" style="left:190px">
      <svg width="50" height="50" viewBox="0 0 50 50"><path d="M6 22L25 6l19 16v22H31V32H19v12H6z" fill="#2b2b2b" stroke="#2b2b2b" stroke-width="3" stroke-linejoin="round"/></svg>HOME</div>
    <div class="nav-item" style="left:366px">
      <svg width="50" height="50" viewBox="0 0 50 50"><path d="M10 4h22l10 10v32H10z" fill="#2b2b2b"/><path d="M17 22h18M17 29h18M17 36h12" stroke="#fff" stroke-width="3"/></svg>OPENINGS</div>
    <div class="nav-item on" style="left:582px">
      <svg width="50" height="50" viewBox="0 0 50 50"><path d="M10 4h22l10 10v32H10z" fill="var(--nav-on)"/><path d="M17 22h18M17 29h18M17 36h12" stroke="#fff" stroke-width="3"/></svg>ASSIGNMENTS</div>
    <div class="nav-item" style="left:807px">
      <svg width="50" height="50" viewBox="0 0 50 50"><circle cx="25" cy="25" r="21" fill="none" stroke="#2b2b2b" stroke-width="4"/><circle cx="25" cy="20" r="7" fill="#2b2b2b"/><path d="M12 39c4-7 22-7 26 0" fill="#2b2b2b"/></svg>SUPPORT</div>
    <div class="nav-item" style="left:988px">
      <svg width="50" height="50" viewBox="0 0 50 50"><path d="M8 4h24v42H8z" fill="#2b2b2b"/><path d="M30 25h16M40 18l7 7-7 7" fill="none" stroke="#2b2b2b" stroke-width="4" stroke-linecap="round" stroke-linejoin="round"/></svg>LOG OUT</div>
  </nav>
</div>
</body>
</html>
```